Wordpress - For IT, Cloud/Hosting, Residential/Commercial Construction Services

We are a holding company for service companies. We want the current Wordpress site modified or a new wordpress site completed. We want this site to be the parent website, that then has pull down menus linking to our other website (currently http://brightwallfix.com, http://q7v.host and would like it to be easy and fluid as we acquire more companies as we have with TKLS, Inc., B&J Construction, Brightwall Fix etc. Model after sites like Pemrose.com, Tallowbine.com, QDV.com,.vanterelm.com

------

The parent is the main site q7v Corp. Below that are sub corps and DBAs. q7v Corp stands for Quick 7 Venture Corp. q7v Offers IT manages services, 24x7 support, Monitoring NOC, Remote Hands, Onsite support services. We have acquired TKLS, Inc, B & J Construction, BrightwallFix.com. We plan to acquire/spin up many companies that offer service, support and installation offerings and will all be known as an q7v Corp Company for branding purposes. We recently had our logo done, but then ran it through 3d glass as we like the look better than the original works. We have original files in vector, but not the 3D galss door render.

Target Market(s)

IT Server and Desktop Support. Construction. Mold Remediation. Mergers and Acquisitions.

Industry/Entity Type

It Company

Coding

Coded - Design and coding required

Font styles to use
Sans Serif

Colors
0792cd

Requirements
Must have
• Clean interface. Modern design. Mobile device and multi browser support. Must be for Wordpress. Job posting with resume submission module.Hook to our Web hosting portal (Tormund) API into VexaLine Reseller portal, customer portal to allow payments to their account etc.. Easy to edit. Easy to add to, Press Release Section, Investor Relations etc.
Should not have
• Slow loading. Played out design. Over use of stock images. Copied from a competitor or something point to such.

```html
<!DOCTYPE html>
<html lang="en">
<head>
<meta charset="utf-8">
<title>Q7V Corp — IT, Cloud Hosting &amp; Construction Services</title>
<link href="https://fonts.googleapis.com/css2?family=Lato:wght@400;700;900&display=swap" rel="stylesheet">
<style>
:root{
  --brand:#0792cd;
  --brand-deep:#1276c0;
  --navy:#1b2a72;
  --navy-dark:#1a237e;
  --ink:#333a45;
  --muted:#6b7280;
  --light:#f3f3f3;
  --footer:#dcdcdc;
  --white:#ffffff;
}
*{box-sizing:border-box;margin:0;padding:0}
html,body{width:1200px;height:3291px;overflow:hidden}
body{font-family:"Lato",sans-serif;color:var(--ink);background:var(--white);position:relative}
.abs{position:absolute}
a{text-decoration:none}
/* hero */
.hero{left:0;top:0;width:1200px;height:678px;background:
  radial-gradient(ellipse 520px 380px at 900px 330px,rgba(40,140,220,.35),transparent 70%),
  linear-gradient(120deg,#1c2574 0%,#1f3f98 45%,#1b77c6 100%)}
.logo{left:182px;top:20px;color:var(--white);font-weight:900;font-size:42px;line-height:1;letter-spacing:1px}
.logo small{display:block;font-size:15px;letter-spacing:15px;margin-top:6px;font-weight:700}
.nav{left:442px;top:41px;display:flex;gap:27px;font-size:15px;font-weight:700;color:var(--white);text-transform:uppercase}
.dropdown{left:443px;top:85px;width:255px;height:211px;background:var(--brand-deep);padding:26px 0 0 42px;z-index:3}
.dropdown::before{content:"";position:absolute;left:28px;top:-10px;border:10px solid transparent;border-top:0;border-bottom-color:var(--brand-deep)}
.dropdown a{display:block;color:var(--white);font-size:17px;margin-bottom:17px}
.hero-art{left:150px;top:150px;width:480px;height:460px;background:
  radial-gradient(ellipse 120px 90px at 330px 330px,rgba(235,242,255,.85),transparent 75%),
  radial-gradient(ellipse 110px 170px at 150px 250px,rgba(150,165,240,.75),transparent 75%),
  radial-gradient(ellipse 110px 170px at 260px 190px,rgba(170,185,250,.7),transparent 75%),
  radial-gradient(ellipse 240px 230px at 240px 240px,rgba(70,90,200,.55),transparent 80%)}
.hero-title{left:658px;top:240px;color:var(--white);font-size:41px;font-weight:700;line-height:42px;text-transform:uppercase}
.hero-text{left:658px;top:340px;color:#c6d6f2;font-size:15px;line-height:19px}
.btn-solid{left:663px;top:407px;width:140px;height:37px;background:var(--brand);color:var(--white);font-size:13px;font-weight:700;display:flex;align-items:center;justify-content:center}
.arrow{width:30px;height:60px}
/* services */
.services{left:0;top:678px;width:1200px;height:305px;background:var(--light)}
.svc{width:200px;text-align:center;color:var(--brand-deep);font-size:15px;font-weight:700;text-transform:uppercase;line-height:17px}
.svc svg.hex{display:block;margin:0 auto 12px}
.chev{display:block;margin:0 auto}
/* about */
.section-title{width:1200px;left:0;text-align:center;font-size:28px;font-weight:900;color:var(--navy);text-transform:uppercase}
.video{left:184px;top:1147px;width:419px;height:248px;background:
  radial-gradient(ellipse 90px 120px at 215px 110px,rgba(250,246,240,.95),transparent 75%),
  radial-gradient(ellipse 70px 120px at 40px 140px,rgba(120,150,170,.7),transparent 75%),
  radial-gradient(ellipse 90px 60px at 330px 200px,rgba(60,60,65,.6),transparent 80%),
  linear-gradient(180deg,#e4e2df 0%,#cfcbc6 55%,#8f8b86 100%)}
.about-text{left:643px;top:1146px;width:370px;font-size:15px;line-height:26px;color:var(--muted)}
.btn-outline{width:169px;height:42px;border:2px solid var(--brand-deep);color:var(--brand-deep);font-size:14px;font-weight:700;display:flex;align-items:center;justify-content:center}
/* why */
.why{left:0;top:1494px;width:1200px;height:476px;background:var(--brand-deep)}
.why-photo{left:439px;top:1494px;width:761px;height:476px;clip-path:polygon(296px 0,761px 0,761px 476px,0 476px);background:
  radial-gradient(ellipse 90px 60px at 390px 60px,rgba(250,250,250,.95),transparent 80%),
  radial-gradient(ellipse 110px 170px at 380px 260px,rgba(40,80,170,.85),transparent 75%),
  radial-gradient(ellipse 120px 170px at 590px 290px,rgba(120,55,30,.85),transparent 75%),
  radial-gradient(ellipse 150px 80px at 500px 320px,rgba(240,238,230,.9),transparent 75%),
  linear-gradient(135deg,#b98b58,#dcb07a 50%,#a87a4a)}
.why-title{left:191px;top:1598px;color:var(--white);font-size:32px;font-weight:400}
.why-text{left:191px;top:1654px;width:420px;color:var(--white);font-size:15px;line-height:26px}
.btn-white{border-color:var(--white);color:var(--white)}
/* news */
.news{left:0;top:1970px;width:1200px;height:520px;background:linear-gradient(180deg,#f6f6f6,#e8edf2)}
.card{top:2100px;width:268px;height:305px;background:var(--white);border:1px solid #cfd3d8}
.card-img{height:173px}
.img-a{background:radial-gradient(ellipse 60px 80px at 150px 80px,rgba(245,235,220,.95),transparent 75%),radial-gradient(ellipse 90px 40px at 130px 150px,rgba(90,90,95,.6),transparent 80%),linear-gradient(180deg,#e6e9ec,#b9bfc6)}
.img-b{background:radial-gradient(ellipse 70px 90px at 120px 60px,rgba(80,110,170,.8),transparent 75%),radial-gradient(ellipse 120px 50px at 130px 150px,rgba(150,110,70,.7),transparent 80%),linear-gradient(180deg,#dfe3e8,#a9afb6)}
.img-c{background:radial-gradient(ellipse 60px 80px at 210px 80px,rgba(210,210,215,.9),transparent 75%),radial-gradient(ellipse 120px 60px at 90px 110px,rgba(40,50,60,.7),transparent 80%),linear-gradient(180deg,#eceef0,#9aa2aa)}
.date{position:absolute;left:0;top:0;width:56px;height:54px;background:#8d9196;color:var(--white);text-align:center;font-size:24px;line-height:24px;padding-top:5px;font-weight:700}
.date span{display:block;font-size:13px;font-weight:400}
.card h3{font-size:17px;font-weight:700;color:#222;margin:14px 20px 6px}
.card p{font-size:11px;line-height:15px;color:var(--muted);margin:0 20px 6px}
.card a{font-size:11px;font-weight:700;color:var(--brand-deep);margin-left:20px}
/* testimonials */
.testi{left:0;top:2490px;width:1200px;height:406px;background:linear-gradient(135deg,#1476c0,#0d5fa8 60%,#1a86cf)}
.quote-box{left:362px;top:2598px;width:487px;height:215px;border:1px solid rgba(255,255,255,.55);background:rgba(10,50,110,.35);color:var(--white);text-align:center;padding:22px 40px 0}
.quote-box .mark{font-size:44px;font-weight:900;line-height:34px}
.quote-box p{font-size:14px;line-height:22px;margin-top:6px}
.quote-box h4{font-size:19px;font-weight:400;margin-top:14px}
.quote-box small{font-size:12px;text-transform:uppercase}
/* footer */
.footer{left:0;top:2896px;width:1200px;height:395px;background:var(--footer)}
.fcol h5{font-size:18px;font-weight:900;color:var(--navy);text-transform:uppercase;margin-bottom:18px}
.fcol li{list-style:none;font-size:13px;color:#444;margin-bottom:13px}
.contact-row{display:flex;gap:12px;font-size:13px;color:#444;line-height:20px;margin-bottom:16px}
.social{display:flex;gap:18px;margin-top:4px}
.social span{width:14px;height:14px;border-radius:50%;background:var(--navy-dark)}
.rule{left:184px;top:3210px;width:838px;height:1px;background:#bdbdbd}
.copy{left:0;top:3241px;width:1200px;text-align:center;font-size:12px;color:#444}
</style>
</head>
<body>

<!-- Hero -->
<section class="abs hero"></section>
<div class="abs logo">Q7V<small>CORP</small></div>
<nav class="abs nav"><span>Company</span><span>Services</span><span>Why Us</span><span>Testimonial</span><span>News</span><span>Contact</span></nav>
<div class="abs hero-art" role="img" aria-label="Isometric illustration of server racks with a cloud"></div>
<div class="abs dropdown">
  <a href="#">q7v.host</a><a href="#">Brightwall Fix</a><a href="#">TKLS, Inc.</a><a href="#">B&amp;J Construction</a>
</div>
<h1 class="abs hero-title">IT &amp; Cloud<br>Hosting Services</h1>
<p class="abs hero-text">Mauris vel lacus vitae felis vestibulum volutpat<br>Etiam est nunc venenatis in tristique</p>
<a class="abs btn-solid">LEARN MORE</a>
<svg class="abs arrow" style="left:100px;top:310px" viewBox="0 0 30 60"><path d="M24 4 6 30l18 26" fill="none" stroke="#fff" stroke-width="2"/></svg>
<svg class="abs arrow" style="left:1066px;top:310px" viewBox="0 0 30 60"><path d="M6 4l18 26L6 56" fill="none" stroke="#fff" stroke-width="2"/></svg>

<!-- Services -->
<section class="abs services"></section>
<div class="abs svc" style="left:165px;top:720px">
  <svg class="hex" width="130" height="118" viewBox="0 0 130 118"><polygon points="33,4 97,4 126,59 97,114 33,114 4,59" fill="#fff" stroke="#d6d6d6" stroke-width="7"/><rect x="45" y="40" width="40" height="30" fill="none" stroke="#1276c0" stroke-width="2.5"/><path d="M58 76h14M65 70v6" stroke="#1276c0" stroke-width="2.5"/></svg>IT Services
  <svg class="chev" style="margin-top:28px" width="30" height="30" viewBox="0 0 30 30"><circle cx="15" cy="15" r="15" fill="#1276c0"/><path d="M9 12l6 6 6-6" fill="none" stroke="#fff" stroke-width="2.5"/></svg></div>
<div class="abs svc" style="left:383px;top:720px">
  <svg class="hex" width="130" height="118" viewBox="0 0 130 118"><polygon points="33,4 97,4 126,59 97,114 33,114 4,59" fill="#fff" stroke="#d6d6d6" stroke-width="7"/><path d="M48 70a10 10 0 0 1 2-20 15 15 0 0 1 29-2 11 11 0 0 1 2 22Z" fill="none" stroke="#1276c0" stroke-width="2.5"/><path d="M65 76V56m-6 6 6-6 6 6" fill="none" stroke="#1276c0" stroke-width="2.5"/></svg>Cloud Hosting
  <svg class="chev" style="margin-top:28px" width="30" height="30" viewBox="0 0 30 30"><circle cx="15" cy="15" r="15" fill="#1276c0"/><path d="M9 12l6 6 6-6" fill="none" stroke="#fff" stroke-width="2.5"/></svg></div>
<div class="abs svc" style="left:600px;top:720px">
  <svg class="hex" width="130" height="118" viewBox="0 0 130 118"><polygon points="33,4 97,4 126,59 97,114 33,114 4,59" fill="#fff" stroke="#d6d6d6" stroke-width="7"/><circle cx="65" cy="59" r="16" fill="none" stroke="#1276c0" stroke-width="2.5"/><circle cx="65" cy="59" r="6" fill="none" stroke="#1276c0" stroke-width="2.5"/><path d="M65 37v6M65 75v6M43 59h6M81 59h6" stroke="#1276c0" stroke-width="3"/></svg>Home/Commercial<br>Services
  <svg class="chev" style="margin-top:11px" width="30" height="30" viewBox="0 0 30 30"><circle cx="15" cy="15" r="15" fill="#1276c0"/><path d="M9 12l6 6 6-6" fill="none" stroke="#fff" stroke-width="2.5"/></svg></div>
<div class="abs svc" style="left:817px;top:720px">
  <svg class="hex" width="130" height="118" viewBox="0 0 130 118"><polygon points="33,4 97,4 126,59 97,114 33,114 4,59" fill="#fff" stroke="#d6d6d6" stroke-width="7"/><path d="M45 78V56l20-16 20 16v22Z" fill="none" stroke="#1276c0" stroke-width="2.5"/><rect x="58" y="62" width="14" height="16" fill="none" stroke="#1276c0" stroke-width="2.5"/></svg>Construction<br>Services
  <svg class="chev" style="margin-top:11px" width="30" height="30" viewBox="0 0 30 30"><circle cx="15" cy="15" r="15" fill="#1276c0"/><path d="M9 12l6 6 6-6" fill="none" stroke="#fff" stroke-width="2.5"/></svg></div>
<svg class="abs" style="left:590px;top:948px" width="22" height="70" viewBox="0 0 22 70"><path d="M11 0v56" stroke="#1b2a72" stroke-width="2"/><circle cx="11" cy="61" r="5" fill="#fff" stroke="#1b2a72" stroke-width="2"/></svg>

<!-- About -->
<h2 class="abs section-title" style="top:1066px">About Our Company</h2>
<div class="abs video" role="img" aria-label="Video still of a smiling consultant at an office desk"></div>
<svg class="abs" style="left:363px;top:1229px" width="60" height="60" viewBox="0 0 60 60"><circle cx="30" cy="30" r="28" fill="#fff"/><path d="M24 18l18 12-18 12Z" fill="#222"/></svg>
<div class="abs about-text">Avscelerisque mi tortor at ipsum cligula augue bibendum accumsan vestibulum ut commodo a mi Morbi ornare gravida elit Integer congue augue et malesuada iaculis ipsum dui aliquet felis at<br><br>cursus magna nisl nec elit Praesent elementum elit at tellus nec ultricies sit amet porttitor mattis</div>
<a class="abs btn-outline" style="left:645px;top:1345px">READ MORE</a>

<!-- Why we are -->
<section class="abs why"></section>
<div class="abs why-photo" role="img" aria-label="Photo of a builder in a hard hat reviewing plans with a client"></div>
<svg class="abs" style="left:590px;top:1470px" width="22" height="66" viewBox="0 0 22 66"><path d="M11 0v50" stroke="#1b2a72" stroke-width="2"/><circle cx="11" cy="56" r="5" fill="#fff" stroke="#1b2a72" stroke-width="2"/></svg>
<h2 class="abs why-title">WHY WE ARE</h2>
<p class="abs why-text">Avscelerisque mi tortor at ipsum cligula augue bibendum accumsan vestibulum ut commodo a mi Morbi ornare gravida elit Integer congue augue et malesuada iaculis ipsum dui aliquet felis at&nbsp; cursus magna nisl nec elit Praesent elementum elit at tellus nec ultricies</p>
<a class="abs btn-outline btn-white" style="left:200px;top:1812px">READ MORE</a>

<!-- News -->
<section class="abs news"></section>
<h2 class="abs section-title" style="top:2032px;color:#111">Latest News</h2>
<article class="abs card" style="left:184px">
  <div class="card-img img-a" role="img" aria-label="Photo of a support agent with a headset at a laptop"></div>
  <div class="date">02<span>AUG</span></div>
  <h3>Your Blog Title here</h3>
  <p>Nulla et malesuada fames ac turpis egestas. Cras id elit donec quis urna ut ante enim dapibus fringilla eu cond</p>
  <a>READ MORE</a>
</article>
<article class="abs card" style="left:470px">
  <div class="card-img img-b" role="img" aria-label="Photo of workers at a construction workbench"></div>
  <div class="date">02<span>AUG</span></div>
  <h3>Your Blog Title here</h3>
  <p>Nulla et malesuada fames ac turpis egestas. Cras id elit donec quis urna ut ante enim dapibus fringilla eu cond</p>
  <a>READ MORE</a>
</article>
<article class="abs card" style="left:755px">
  <div class="card-img img-c" role="img" aria-label="Photo of a network operations desk with monitors"></div>
  <div class="date">02<span>AUG</span></div>
  <h3>Your Blog Title here</h3>
  <p>Nulla et malesuada fames ac turpis egestas. Cras id elit donec quis urna ut ante enim dapibus fringilla eu cond</p>
  <a>READ MORE</a>
</article>

<!-- Testimonials -->
<section class="abs testi"></section>
<h2 class="abs section-title" style="top:2530px;color:#fff;font-size:24px">Testimonials</h2>
<div class="abs quote-box">
  <div class="mark">&ldquo;</div>
  <p>Avscelerisque mi tortor at ipsum cligula augue bibendum accumsan vestibulum ut commodo a mi Morbi ornare gravida elit Integer congue augue et malesuada iaculis ipsum</p>
  <h4>BY AUTHOR NAME</h4>
  <small>Company Name</small>
</div>
<svg class="abs" style="left:286px;top:2672px" width="20" height="36" viewBox="0 0 20 36"><path d="M17 2 3 18l14 16" fill="none" stroke="#fff" stroke-width="3"/></svg>
<svg class="abs" style="left:888px;top:2672px" width="20" height="36" viewBox="0 0 20 36"><path d="M3 2l14 16L3 34" fill="none" stroke="#fff" stroke-width="3"/></svg>

<!-- Footer -->
<footer class="abs footer"></footer>
<div class="abs fcol" style="left:197px;top:2964px">
  <h5>Contact Us</h5>
  <div class="contact-row"><svg width="14" height="20" viewBox="0 0 14 20"><path d="M7 19S1 11 1 7a6 6 0 0 1 12 0c0 4-6 12-6 12Z" fill="#1a237e"/><circle cx="7" cy="7" r="2.2" fill="#dcdcdc"/></svg><span>245 E 14th Street #3B<br>Texas 10031 TX</span></div>
  <div class="contact-row"><svg width="16" height="16" viewBox="0 0 16 16"><path d="M3 1l3 3-2 2a9 9 0 0 0 6 6l2-2 3 3-2 2C6 15 1 10 1 3Z" fill="none" stroke="#1a237e" stroke-width="1.4"/></svg><span>555.204.7731</span></div>
  <div class="contact-row"><svg width="16" height="16" viewBox="0 0 16 16"><rect x="1" y="3" width="14" height="10" fill="none" stroke="#1a237e" stroke-width="1.4"/><path d="M1 3l7 6 7-6" fill="none" stroke="#1a237e" stroke-width="1.4"/></svg><span>info@companyname.com</span></div>
</div>
<div class="abs fcol" style="left:507px;top:2964px"><h5>Company</h5><ul><li>Home</li><li>About Us</li><li>Our Services</li><li>Why We Are</li></ul></div>
<div class="abs fcol" style="left:689px;top:2964px"><h5>Resources</h5><ul><li>Testimonials</li><li>Blogs</li><li>News</li><li>Conact Us</li></ul></div>
<div class="abs fcol" style="left:897px;top:2964px"><h5>Legal</h5><ul><li>Terms</li><li>Legal</li><li>Privacy Policy</li></ul><div class="social"><span></span><span></span><span></span></div></div>
<div class="abs rule"></div>
<p class="abs copy">© 2018 Company Name&nbsp; All right reserved</p>

</body>
</html>
```